holloway paving service

Needs to have phone number 0418259730 and email markholloway@brightmail.com.au.
ABN 62318470915
name mark holloway

For all your concreting solutions
Excavation
Exposed & colour concrete
House & shed slabs
Driveways
Landing & steps

Contact Information for Business Card

ph 0418259730
email markholloway@brightmail.com.au.
ABN 62318470915
name mark holloway

```html
<!DOCTYPE html>
<html lang="en">
<head>
<meta charset="utf-8">
<title>Holloway Paving Service – Business Card</title>
<link rel="stylesheet" href="https://fonts.googleapis.com/css2?family=Mada:wght@600;700&family=Questrial&display=swap">
<style>
  :root {
    --bg: #e9e6e2;
    --paper-light: #f4f4f4;
    --paper-mid: #dcdcdc;
    --slate: #4f4f51;
    --orange: #e8642a;
    --orange-deep: #d9561d;
    --orange-light: #f07c3f;
    --text-grey: #555557;
    --white: #ffffff;
  }
  * { box-sizing: border-box; margin: 0; padding: 0; }
  html, body { width: 1200px; height: 960px; overflow: hidden; }
  body { background: var(--bg); position: relative; font-family: "Questrial", sans-serif; }

  .card { position: absolute; overflow: hidden; box-shadow: 0 6px 14px rgba(0,0,0,.25); }

  /* Front */
  .card-front {
    left: 302px; top: 127px; width: 600px; height: 340px;
    background: linear-gradient(120deg, var(--paper-mid) 0%, var(--paper-light) 45%, var(--paper-mid) 100%);
  }
  .front-band {
    position: absolute; right: 0; top: 0; width: 172px; height: 100%;
    background: var(--slate);
  }
  .brand-block { position: absolute; left: 34px; top: 36px; width: 274px; text-align: center; }
  .brand-name {
    font-family: "Mada", sans-serif; font-weight: 700; font-size: 25px;
    color: var(--orange); letter-spacing: .6px; line-height: 1; white-space: nowrap;
  }
  .brand-sub {
    display: flex; align-items: center; gap: 10px; margin-top: 3px;
    font-family: "Questrial", sans-serif; font-size: 17px; letter-spacing: 3px;
    color: var(--text-grey); line-height: 1;
  }
  .brand-sub::before, .brand-sub::after { content: ""; flex: 1; height: 2px; background: var(--text-grey); }
  .brand-phone {
    margin-top: 2px; font-family: "Questrial", sans-serif; font-size: 17px;
    letter-spacing: 1.5px; color: var(--orange); line-height: 1;
  }
  .brand-mark {
    position: absolute; right: 0; top: 0; width: 172px; height: 100%;
    display: flex; align-items: center; justify-content: center; gap: 10px;
  }
  .brand-mark .mark-square { width: 18px; height: 18px; background: var(--orange); flex: none; }
  .brand-mark .mark-name {
    font-family: "Mada", sans-serif; font-weight: 700; font-size: 24px;
    color: var(--white); line-height: 1.05;
  }
  .contact { position: absolute; left: 35px; top: 240px; }
  .contact-name {
    font-family: "Mada", sans-serif; font-weight: 700; font-size: 23px;
    color: var(--orange); line-height: 1; margin-bottom: 6px;
  }
  .contact-line { font-size: 14px; color: var(--text-grey); line-height: 21px; letter-spacing: .3px; }

  /* Back */
  .card-back {
    left: 300px; top: 500px; width: 598px; height: 342px;
    background: linear-gradient(90deg, var(--orange-deep) 0%, var(--orange-light) 55%, var(--orange-deep) 100%);
  }
  .back-pattern { position: absolute; inset: 0; background: linear-gradient(160deg, rgba(255,255,255,.04), rgba(0,0,0,.06)); }
  .back-mark {
    position: absolute; left: 128px; top: 156px;
    display: flex; align-items: center; gap: 8px;
  }
  .back-mark .mark-square { width: 14px; height: 14px; background: var(--white); }
  .back-mark .mark-name {
    font-family: "Questrial", sans-serif; font-size: 16px; color: var(--white); line-height: 1;
  }
  .services { position: absolute; left: 252px; top: 125px; list-style: none; }
  .services li {
    font-size: 14.5px; color: var(--white); line-height: 18px; letter-spacing: .4px;
    display: flex; align-items: center; gap: 7px;
  }
  .services li::before {
    content: ""; width: 5px; height: 5px; background: var(--white); transform: rotate(45deg);
  }
</style>
</head>
<body>
  <section class="card card-front">
    <div class="front-band"></div>
    <div class="brand-block">
      <div class="brand-name">HOLLOWAY PAVING</div>
      <div class="brand-sub">SERVICE</div>
      <div class="brand-phone">0418259730</div>
    </div>
    <div class="brand-mark">
      <span class="mark-square"></span>
      <span class="mark-name">Holloway<br>Paving</span>
    </div>
    <div class="contact">
      <div class="contact-name">MARK HOLLOWAY</div>
      <div class="contact-line">markholloway@brightmail.com.au</div>
      <div class="contact-line">ABN 62318470915</div>
    </div>
  </section>

  <section class="card card-back">
    <div class="back-pattern" role="img" aria-label="Faint repeating diamond pattern in orange tones"></div>
    <div class="back-mark">
      <span class="mark-square"></span>
      <span class="mark-name">Holloway</span>
    </div>
    <ul class="services">
      <li>Excavation</li>
      <li>Exposed &amp; colour concrete</li>
      <li>House &amp; shed slabs</li>
      <li>Driveways</li>
      <li>Landing &amp; steps</li>
    </ul>
  </section>
</body>
</html>
```